Interior designer needs a power point template design

I need a template PowerPoint design for my client presentations. The presentations I prepare for my clients usually include the furniture project, the detail of the selected furniture, and the costs. There are a lot of images I insert. What I need is to have a template that I can use for all my presentations, where from time to time I will insert the specific images and descriptions I want to insert. What will always be the same will be the cover, the colors, the font, and the design of the internal sections.
I already have my logo that I would like to insert on each page of the presentation (in small size).
In summary, I need:
- basic template design
- cover with an image chosen by Pictavale photo
- design an internal section/chapter
- internal page design.

I like the clolors of pink and brown <8please see image attached)
Images (will come from Pictavale photo)
● entrance/hall
● living room
● dining room
● Bathroom
● Closet
● Kids room
● Master bedroom
● Master bathroom
● Kitchen
● Office
● Laundry
● Balcony or Terrace

Target Market(s)

Customers (both residential and commercial projects)

Industry/Entity Type

interior design

Font styles to use
Other font styles liked:
• I like courier new

Requirements
Must have
• beautiful design
Should not have
• animations

```html
<!DOCTYPE html>
<html lang="it">
<head>
<meta charset="utf-8">
<title>Casa Lumen – modello presentazione</title>
<link rel="stylesheet" href="https://fonts.googleapis.com/css2?family=Gelasio:wght@400&family=Courier+Prime&display=swap">
<style>
:root{
  --board:#4d4d4d;
  --paper:#ffffff;
  --rose:#c68a77;
  --brown:#8b3a0f;
  --ink:#3a3a3a;
  --mark:#8a8a8a;
  --serif:'Gelasio', Georgia, serif;
  --mono:'Courier Prime', 'Courier New', monospace;
}
*{margin:0;padding:0;box-sizing:border-box}
html,body{width:1200px;height:1200px;overflow:hidden;background:var(--board)}
.board{position:relative;width:1200px;height:1200px}
.slide{position:absolute;width:376px;height:211px;background:var(--paper);overflow:hidden}
.slide *{position:absolute}
.block{background:var(--rose)}
.media{display:block}
.kicker{font-family:var(--mono);font-weight:400;color:var(--brown);font-size:8px;line-height:1;white-space:nowrap}
.title{font-family:var(--serif);font-weight:400;color:var(--brown);font-size:27px;line-height:34px;white-space:nowrap}
.caption{font-family:var(--mono);font-weight:400;color:var(--ink);font-size:6.4px;line-height:8.4px;white-space:nowrap}
.caption.light{color:#fff}
.mark{width:24px;display:flex;flex-direction:column;align-items:center;gap:3px}
.mark > *{position:static}
.mark .ring{width:16px;height:16px;border:1px solid var(--mark);border-radius:50%}
.mark .name{font-family:var(--mono);color:var(--mark);font-size:5px;line-height:1;text-align:center;white-space:nowrap}
.cover{left:196px;top:32px;width:807px;height:454px}
.cover .title{font-size:56px;line-height:70px}
.cover .kicker{font-size:16px}
.cover .mark{width:60px;gap:8px}
.cover .mark .ring{width:42px;height:42px}
.cover .mark .name{font-size:10px}
</style>
</head>
<body>
<div class="board">

  <!-- Cover -->
  <section class="slide cover">
    <svg class="media" style="left:0;top:0" width="396" height="454" role="img" aria-label="Illustrazione di una camera da letto luminosa con piante e finestra">
      <defs><linearGradient id="gCover" x1="0" y1="0" x2="0" y2="1"><stop offset="0" stop-color="#fde7cf"/><stop offset="1" stop-color="#f6d3ae"/></linearGradient></defs>
      <rect width="396" height="454" fill="url(#gCover)"/>
    </svg>
    <div class="block" style="left:378px;top:123px;width:73px;height:261px"></div>
    <p class="kicker" style="left:507px;top:162px">Interior</p>
    <h1 class="title" style="left:498px;top:190px">Camera<br>padronale</h1>
    <div class="mark" style="left:727px;top:30px"><span class="ring"></span><span class="name">CASA<br>LUMEN</span></div>
  </section>

  <!-- Row 1 -->
  <section class="slide" style="left:22px;top:510px">
    <div class="block" style="left:0;top:0;width:130px;height:160px"></div>
    <svg class="media" style="left:77px;top:53px" width="132" height="140" role="img" aria-label="Render della camera padronale con carta da parati e lampadario">
      <defs><linearGradient id="gA" x1="0" y1="0" x2="0" y2="1"><stop offset="0" stop-color="#d9dde2"/><stop offset=".6" stop-color="#4a5563"/><stop offset="1" stop-color="#a6773f"/></linearGradient></defs>
      <rect width="132" height="140" fill="url(#gA)"/>
    </svg>
    <p class="kicker" style="left:227px;top:63px">Interior</p>
    <h2 class="title" style="left:226px;top:70px">Camera<br>padronale</h2>
    <p class="caption" style="left:226px;top:146px">L'arredamento<br>della camera padronale</p>
    <div class="mark" style="left:337px;top:10px"><span class="ring"></span><span class="name">CASA<br>LUMEN</span></div>
    <div class="block" style="left:340px;top:180px;width:36px;height:31px"></div>
  </section>

  <section class="slide" style="left:412px;top:512px">
    <div class="block" style="left:19px;top:20px;width:170px;height:171px"></div>
    <svg class="media" style="left:32px;top:32px" width="142" height="112" role="img" aria-label="Illustrazione di un bagno con vasca e piante">
      <defs><linearGradient id="gB" x1="0" y1="0" x2="0" y2="1"><stop offset="0" stop-color="#f7f7f5"/><stop offset="1" stop-color="#cfe6ec"/></linearGradient></defs>
      <rect width="142" height="112" fill="url(#gB)"/>
    </svg>
    <p class="caption light" style="left:58px;top:160px">L'arredamento<br>della cabina armadio</p>
    <p class="kicker" style="left:200px;top:23px">Interior</p>
    <h2 class="title" style="left:199px;top:30px">Bagno<br>padronale</h2>
    <p class="caption" style="left:206px;top:131px">L'arredamento<br>della cabina armadio</p>
    <div class="mark" style="left:337px;top:10px"><span class="ring"></span><span class="name">CASA<br>LUMEN</span></div>
    <div class="block" style="left:340px;top:181px;width:36px;height:30px"></div>
  </section>

  <section class="slide" style="left:801px;top:512px">
    <svg class="media" style="left:12px;top:0" width="149" height="211" role="img" aria-label="Render della camera padronale con letto e lampadario">
      <defs><linearGradient id="gC" x1="0" y1="0" x2="0" y2="1"><stop offset="0" stop-color="#c9d3dc"/><stop offset=".45" stop-color="#dfe2e6"/><stop offset=".75" stop-color="#4b525c"/><stop offset="1" stop-color="#a87a45"/></linearGradient></defs>
      <rect width="149" height="211" fill="url(#gC)"/>
    </svg>
    <p class="kicker" style="left:193px;top:41px">Interior</p>
    <h2 class="title" style="left:191px;top:48px">Camera<br>padronale</h2>
    <div class="block" style="left:140px;top:121px;width:213px;height:75px"></div>
    <p class="caption light" style="left:140px;top:150px;width:213px;text-align:center">L'arredamento<br>della camera padronale</p>
    <div class="mark" style="left:337px;top:10px"><span class="ring"></span><span class="name">CASA<br>LUMEN</span></div>
  </section>

  <!-- Row 2 -->
  <section class="slide" style="left:22px;top:735px">
    <svg class="media" style="left:0;top:0" width="156" height="124" role="img" aria-label="Render del bagno padronale con lavabo e doccia">
      <defs><linearGradient id="gD" x1="0" y1="0" x2="0" y2="1"><stop offset="0" stop-color="#3c3f44"/><stop offset=".55" stop-color="#8e9196"/><stop offset="1" stop-color="#d8d8d8"/></linearGradient></defs>
      <rect width="156" height="124" fill="url(#gD)"/>
    </svg>
    <div class="block" style="left:156px;top:0;width:220px;height:107px"></div>
    <p class="caption light" style="left:200px;top:38px">L'arredamento<br>della cabina armadio</p>
    <div style="left:332px;top:4px;width:32px;height:45px;background:#fff"></div>
    <div class="mark" style="left:336px;top:10px"><span class="ring"></span><span class="name">CASA<br>LUMEN</span></div>
    <h2 class="title" style="left:32px;top:126px">Bagno<br>padronale</h2>
    <svg class="media" style="left:198px;top:86px" width="76" height="125" role="img" aria-label="Render del bagno con vasca e lampadario">
      <defs><linearGradient id="gD2" x1="0" y1="0" x2="0" y2="1"><stop offset="0" stop-color="#3a3d42"/><stop offset=".6" stop-color="#a3a5a8"/><stop offset="1" stop-color="#e6e6e6"/></linearGradient></defs>
      <rect width="76" height="125" fill="url(#gD2)"/>
    </svg>
    <div class="block" style="left:340px;top:180px;width:36px;height:31px"></div>
  </section>

  <section class="slide" style="left:412px;top:735px">
    <div class="block" style="left:0;top:0;width:129px;height:211px"></div>
    <svg class="media" style="left:37px;top:32px" width="135" height="145" role="img" aria-label="Foto di una cabina armadio con abiti e scarpe">
      <defs><linearGradient id="gE" x1="0" y1="0" x2="1" y2="0"><stop offset="0" stop-color="#2a2a2c"/><stop offset=".5" stop-color="#6f7684"/><stop offset="1" stop-color="#d9d4cc"/></linearGradient></defs>
      <rect width="135" height="145" fill="url(#gE)"/>
    </svg>
    <h2 class="title" style="left:188px;top:34px">Camera<br>Armadio</h2>
    <p class="caption" style="left:194px;top:132px">L'arredamento<br>della cabina armadio</p>
    <div class="mark" style="left:337px;top:10px"><span class="ring"></span><span class="name">CASA<br>LUMEN</span></div>
    <div class="block" style="left:332px;top:57px;width:44px;height:154px"></div>
  </section>

  <section class="slide" style="left:801px;top:735px">
    <div class="block" style="left:22px;top:72px;width:136px;height:82px"></div>
    <svg class="media" style="left:2px;top:16px" width="135" height="114" role="img" aria-label="Render di una cabina armadio con appendiabiti e scaffali">
      <defs><linearGradient id="gF" x1="0" y1="0" x2="0" y2="1"><stop offset="0" stop-color="#f1f1f1"/><stop offset=".5" stop-color="#4d535c"/><stop offset="1" stop-color="#e5e5e5"/></linearGradient></defs>
      <rect width="135" height="114" fill="url(#gF)"/>
    </svg>
    <p class="caption" style="left:29px;top:174px">L'arredamento della camera<br>padronale</p>
    <h2 class="title" style="left:196px;top:50px">Camera<br>Armadio</h2>
    <p class="caption" style="left:196px;top:136px">L'arredamento<br>della cabina armadio</p>
    <div class="mark" style="left:337px;top:10px"><span class="ring"></span><span class="name">CASA<br>LUMEN</span></div>
    <div class="block" style="left:340px;top:180px;width:36px;height:31px"></div>
  </section>

  <!-- Row 3 -->
  <section class="slide" style="left:22px;top:963px">
    <div class="block" style="left:0;top:53px;width:38px;height:106px"></div>
    <div class="block" style="left:185px;top:0;width:95px;height:104px"></div>
    <svg class="media" style="left:217px;top:16px" width="89" height="178" role="img" aria-label="Render del bagno con vasca freestanding e pavimento decorato">
      <defs><linearGradient id="gG" x1="0" y1="0" x2="0" y2="1"><stop offset="0" stop-color="#3b3e43"/><stop offset=".45" stop-color="#c7ccd2"/><stop offset=".8" stop-color="#efefef"/><stop offset="1" stop-color="#6b6b6b"/></linearGradient></defs>
      <rect width="89" height="178" fill="url(#gG)"/>
    </svg>
    <h2 class="title" style="left:52px;top:28px">Bagno<br>padronale</h2>
    <p class="caption" style="left:52px;top:135px">L'arredamento<br>della cabina armadio</p>
    <div class="mark" style="left:337px;top:10px"><span class="ring"></span><span class="name">CASA<br>LUMEN</span></div>
    <div class="block" style="left:340px;top:173px;width:36px;height:38px"></div>
  </section>

  <section class="slide" style="left:412px;top:963px">
    <h2 class="title" style="left:24px;top:21px">Camera<br>Armadio</h2>
    <div class="block" style="left:0;top:95px;width:184px;height:93px"></div>
    <p class="caption" style="left:219px;top:51px">L'arredamento della<br>cabina armadio</p>
    <svg class="media" style="left:217px;top:76px" width="159" height="135" role="img" aria-label="Illustrazione di uno stand appendiabiti con vestiti, specchio e pianta">
      <defs><linearGradient id="gH" x1="0" y1="0" x2="0" y2="1"><stop offset="0" stop-color="#f7e8e3"/><stop offset="1" stop-color="#f0d9cf"/></linearGradient></defs>
      <rect width="159" height="135" fill="url(#gH)"/>
    </svg>
    <div class="mark" style="left:337px;top:10px"><span class="ring"></span><span class="name">CASA<br>LUMEN</span></div>
  </section>

  <section class="slide" style="left:801px;top:963px">
    <div class="block" style="left:0;top:20px;width:76px;height:30px"></div>
    <h2 class="title" style="left:49px;top:59px">Casa<br>Lumen</h2>
    <p class="caption" style="left:49px;top:140px">di Marta Valdieri<br>via delle Rose, 24<br><span style="position:static;color:#2a5db0;text-decoration:underline">martavaldieri@posta.example</span></p>
    <p class="caption" style="left:49px;top:172px">333/5108264</p>
    <div class="block" style="left:197px;top:0;width:179px;height:211px"></div>
    <div style="left:226px;top:20px;width:120px;height:171px;background:#fff;display:flex;flex-direction:column;align-items:center;justify-content:center;gap:14px">
      <span style="position:static;width:72px;height:72px;border:1px solid var(--mark);border-radius:50%"></span>
      <span style="position:static;font-family:var(--mono);color:var(--mark);font-size:15px;line-height:18px;letter-spacing:2px;text-align:center">CASA<br>LUMEN</span>
    </div>
  </section>

</div>
</body>
</html>
```